High Tech Real Estate Startup needs a business card

We are developing an innovative real estate marketing product based around advanced search and virtual reality.

We talk to people, we need business cards.

Target Market(s)

The target market is technology professionals and realtors.

Contact Information for Business Card

The information to be included will include

Name
Title
Phone Number
E-mail Address
www.zelquin.com

It should use simple iconography for each one of those fields.

Font styles to use
Other font styles liked:
• Co, Jubilat, Avenir

Colors

Designer to choose colors to be used in the design.

Requirements
Must have
• Clean aesthetic,
• Good use of negative space.
• It should use our company logo, shown in the attached file. It is able to use the negative of that logo (coloured font and white background) and I have attached other acceptable accent colours in a swatch file.
Should not have
• Should not be too busy
• No extraneous text (slogans, tag lines etc)

```html
<!DOCTYPE html>
<html lang="en">
<head>
<meta charset="utf-8">
<title>Zelquin Business Card</title>
<link rel="stylesheet" href="https://fonts.googleapis.com/css2?family=Montserrat:wght@500;600&family=Inter:wght@400;600&display=swap">
<style>
  :root {
    --teal: #17b3bd;
    --charcoal: #232323;
    --paper: #ffffff;
    --ink: #1c1c1c;
    --backdrop: #e9e8e6;
  }
  * { box-sizing: border-box; margin: 0; padding: 0; }
  html, body {
    width: 1200px; height: 930px; overflow: hidden;
    background: var(--backdrop);
  }
  .canvas { position: relative; width: 1200px; height: 930px; }

  .card {
    position: absolute;
    width: 560px; height: 320px;
    border-radius: 18px;
    overflow: hidden;
    box-shadow: 0 10px 28px rgba(0,0,0,.18);
  }

  /* Back of card */
  .card-back { left: 80px; top: 110px; background: var(--charcoal); }
  .card-back .network-pattern {
    position: absolute; inset: 0;
    background: radial-gradient(ellipse at 40% 45%, rgba(120,120,120,.22), transparent 55%),
                radial-gradient(ellipse at 80% 20%, rgba(120,120,120,.16), transparent 45%);
  }
  .wordmark {
    font-family: "Montserrat", sans-serif;
    font-weight: 500;
    color: var(--teal);
    letter-spacing: 2px;
    line-height: 1;
  }
  .card-back .wordmark {
    position: absolute; left: 0; right: 0; top: 132px;
    text-align: center; font-size: 58px;
  }

  /* Front of card */
  .card-front { left: 560px; top: 500px; background: var(--paper); }
  .swoosh { position: absolute; left: 0; top: 0; width: 560px; height: 320px; }
  .card-front .wordmark {
    position: absolute; left: 40px; top: 128px; font-size: 50px;
  }
  .divider {
    position: absolute; left: 320px; top: 52px;
    width: 2px; height: 124px; background: var(--teal);
  }
  .contact {
    position: absolute; left: 336px; top: 34px;
    font-family: "Inter", sans-serif; color: var(--ink);
    font-size: 12px; line-height: 16px;
  }
  .contact .name {
    font-family: "Montserrat", sans-serif; font-weight: 600;
    color: var(--teal); font-size: 16px; line-height: 20px;
    text-transform: uppercase;
  }
  .contact .title { margin-bottom: 3px; padding-left: 10px; }
  .contact .address { padding-left: 20px; margin-bottom: 3px; }
  .contact ul { list-style: none; padding-left: 30px; }
  .contact li { display: flex; align-items: center; gap: 6px; }
  .contact li svg { width: 10px; height: 10px; flex: none; }
</style>
</head>
<body>
<main class="canvas">
  <section class="card card-back" aria-label="Card back">
    <div class="network-pattern" role="img" aria-label="Faint grey connected-dot network pattern"></div>
    <div class="wordmark">ZELQUIN</div>
  </section>

  <section class="card card-front" aria-label="Card front">
    <svg class="swoosh" viewBox="0 0 560 320" aria-hidden="true">
      <path d="M0 272 Q330 256 560 188 L560 320 L0 320 Z" fill="var(--charcoal)"/>
      <path d="M170 262 Q400 238 560 164 L560 178 Q400 248 170 262 Z" fill="var(--teal)"/>
    </svg>

    <div class="wordmark">ZELQUIN</div>
    <div class="divider"></div>

    <div class="contact">
      <p class="name">Dorian Vale</p>
      <p class="title">Director</p>
      <p class="address">560 Alder Creek Rd.<br>Fairview, OR 97024</p>
      <ul>
        <li>
          <svg viewBox="0 0 10 10"><path d="M2 1 L4 1 L4.6 3 L3.4 3.8 Q4.3 5.8 6.2 6.6 L7 5.4 L9 6 L9 8 Q9 9 8 9 Q1 8.6 1 2 Q1 1 2 1Z" fill="var(--teal)"/></svg>
          +1-555-204-7719
        </li>
        <li>
          <svg viewBox="0 0 10 10"><rect x="1" y="2" width="8" height="6" fill="none" stroke="var(--teal)" stroke-width="1.2"/><path d="M1 2 L5 5.5 L9 2" fill="none" stroke="var(--teal)" stroke-width="1.2"/></svg>
          info@zelquin.com
        </li>
        <li>
          <svg viewBox="0 0 10 10"><circle cx="5" cy="5" r="4" fill="none" stroke="var(--teal)" stroke-width="1"/><ellipse cx="5" cy="5" rx="1.8" ry="4" fill="none" stroke="var(--teal)" stroke-width="0.8"/><path d="M1 5 H9" stroke="var(--teal)" stroke-width="0.8"/></svg>
          www.zelquin.com
        </li>
      </ul>
    </div>
  </section>
</main>
</body>
</html>
```